A website where experts collaborate on your project

I am building a new website where experts (yes, like designers) collaborate on projects with the project owner. More minds = more collaboration = better end product. Please see Pelmora(dot)com for a quick landing page I created for collaborating on presentations (although there will be many project types offered)

I am looking for a DESIGNER LONG TERM, but for now, just need initial mock ups to show the web programmers.

I have 21 Word documents loosely designed, what I would like to see here is a theme. Please DO NOT GO OFF WHAT YOU CURRENTLY SEE AT PELMORA. What is up now is only a quick landing page.

You can view a Word doc of the homepage here:
https://www.filevanta.com/s/qx83kdm2/home.docx?dl=0

WHAT AM I LOOKING FOR?
A clean, well designed theme.

Here is a link to the logo:
https://www.filevanta.com/s/mr47tpz9/logo%20-%20horizontal.tif?dl=0
-----------------------------------------
Here are a few sites I like the design of and what I like about them:
www.quenbrook.com-all around my favorite, beautiful graphics, clean layout, bold use of colors on a dark background
Ravelto.com- clean layout, The use of humans and bubble style elements.
Mintharbor.com :) clean, bold, unique pop art style but professional
plumevault.com - From the unique colors and artwork and the ability of that art to not interfere with the important elements of the site
sparkwidgets.com-clean, nice colors, well organized and separated sections.
www.dunmereco.com-love the font, use of colors and sectionalized style

All in all, I am not picky and open to so many styles. I would ultimately like the designer I pick to design all 21 pages.
Updates

Hello everyone,Moving forward, I would like you all to pay special attention to the section in my brief titled "Here are a few sites I like the design of and what I like about them". Please see below, I handpicked each one of these as sites I really like. Thank you.Here are a few sites I like the design of and what I like about them:Ravelto.com- clean layout, The use of humans and bubble style elements.Mintharbor.com :) clean, bold, unique pop art style but professionalwriteraccess.com - From the unique colors and artwork and the ability of that art to not interfere with the important elements of the sitegrowthgeeks.com-clean, nice colors, well organized and separated sections.www.dunmereco.com-love the font, use of colors and sectionalized stylewww.quenbrook.com-beautiful graphics, clean layout, bold use of colors----------------------------------------- Added Tuesday, November 24, 2015

I updated the homepage, you can see it here:https://www.dropbox.com/s/kwlkbsookq3cg2m/1new%20homepage.docx?dl=0I am modeling it after my favorite designed site: triplelift.comI love the dark colors with the orange glowing style boldness of the buttons. It's real clean too. Added Tuesday, November 24, 2015

Target Market(s)

small business owners, marketers, freelancer writers, graphic designers,

Industry/Entity Type

Building

Number of Pages Required

5+ page

Requirements
Must have
• I can't think of anything the project must have.
Nice to have
• WHAT AM I LOOKING FOR?
• A clean, well designed theme. I had a designer do a bit of work putting elements together, I found it to be very plain, but I like the Application Page (https://www.filevanta.com/s/jb19ckr3/Pelmora-Website.ai?dl=0)
• Here is a link to the logo:
• https://www.filevanta.com/s/mr47tpz9/logo%20-%20horizontal.tif?dl=0
• Here are a few sites I like the design of and what I like about them:
• Ravelto.com- clean layout, The use of humans and bubble style elements.
• Mintharbor.com :) clean, bold, unique pop art style but professional
• plumevault.com - From the unique colors and artwork and the ability of that art to not interfere with the important elements of the site
• sparkwidgets.com-clean, nice colors, well organized and separated sections.
• www.dunmereco.com-love the font, use of colors and sectionalized style
• www.quenbrook.com-beautiful graphics, clean layout, bold use of colors
• -----------------------------------------
Should not have
• out of the boxed, templated style website. I want this site to be memorable and not look like a thousand others

```html
<!DOCTYPE html>
<html lang="en">
<head>
<meta charset="utf-8">
<title>Pelmora – Experts collaborating on your project</title>
<link href="https://fonts.googleapis.com/css2?family=Roboto:wght@300;400;500;700&family=Oswald:wght@600&display=swap" rel="stylesheet">
<style>
:root{
  --orange:#eb9b12;
  --blue:#6bb3cf;
  --dark:#2a2a2a;
  --footer:#353535;
  --text:#555;
  --line:#dcdcdc;
  --white:#fff;
  --pale:#f2f8fb;
}
*{box-sizing:border-box;margin:0;padding:0}
html,body{width:673px;height:1200px;overflow:hidden;background:var(--white);font-family:'Roboto',Arial,sans-serif;color:var(--text)}
.page{position:relative;width:673px;height:1200px}
.abs{position:absolute}

/* header */
.brand{left:55px;top:34px;display:flex;align-items:center;gap:6px}
.brand-name{font-size:15px;font-weight:500;color:var(--orange);letter-spacing:.3px}
.brand-dot{width:30px;height:30px;border-radius:50%;background:var(--orange)}
.notice{left:333px;top:15px;width:177px;height:49px;background:var(--blue);border-radius:3px;color:var(--white);font-size:5.4px;line-height:8px;padding:7px 7px}
.notice-tail{left:360px;top:63px}
.home-btn{left:554px;top:27px;width:63px;height:23px;background:var(--orange);border-radius:2px;color:var(--white);font-size:10px;display:flex;align-items:center;justify-content:center;gap:4px}

.navbar{left:0;top:78px;width:673px;height:36px;background:var(--dark)}
.search{left:55px;top:85px;width:127px;height:22px;border:1px solid #ccc;background:var(--dark);color:#aaa;font-size:6px;font-style:italic;padding:7px 6px}
.search-btn{left:182px;top:85px;width:22px;height:22px;background:var(--orange);display:flex;align-items:center;justify-content:center}
.nav-chat{left:360px;top:89px}
.nav-link{top:92px;font-size:7px;font-weight:500;color:var(--white)}

/* hero */
.hero{left:0;top:114px;width:673px;height:338px;background:linear-gradient(90deg,#6d8a3c 0%,#9fb86a 35%,#b8cf8a 55%,#e9ecec 72%,#f3f4f2 100%)}
.hero-title{left:55px;top:160px;font-family:'Oswald',sans-serif;font-weight:600;font-size:21px;color:var(--orange);letter-spacing:-.2px}
.hero-sub{left:55px;top:192px;font-size:12.5px;line-height:16px;color:var(--white);text-shadow:0 1px 2px rgba(0,0,0,.5)}
.hero-btn{left:55px;top:238px;width:68px;height:24px;background:var(--blue);border-radius:2px;color:var(--white);font-size:7px;font-weight:500;display:flex;align-items:center;justify-content:center}
.hero-card{left:55px;top:304px;width:285px;height:89px;background:rgba(40,40,40,.88);border-radius:3px;text-align:center;padding:12px 24px}
.hero-card h2{font-size:10px;font-weight:500;color:var(--white);margin-bottom:5px}
.hero-card .roles{font-size:7.6px;color:var(--orange);margin-bottom:6px}
.hero-card p{font-size:5.6px;line-height:10px;color:#ddd}
.hero-tail{left:176px;top:393px}
.dot{top:427px;width:8px;height:8px;border-radius:50%;background:var(--blue)}

/* filters */
.filters{left:55px;top:486px;width:187px;height:281px;border:1px solid #d6d6d6}
.filters-head{height:30px;background:var(--orange);color:var(--white);font-size:10px;font-weight:500;display:flex;align-items:center;justify-content:space-between;padding:0 11px}
.price{padding:8px 11px 0;height:58px;border-bottom:1px solid var(--line)}
.price-label{font-size:7.5px;color:#333;font-weight:500}
.slider{position:relative;height:14px;margin-top:4px}
.slider .track{position:absolute;left:2px;right:0;top:5px;height:5px;border-radius:3px;background:#bbb}
.slider .fill{position:absolute;left:2px;width:104px;top:5px;height:5px;border-radius:3px;background:var(--blue)}
.slider .knob{position:absolute;top:2px;width:10px;height:10px;border-radius:50%;background:var(--blue)}
.price-values{display:flex;justify-content:space-between;font-size:6.8px;color:#333;margin-top:2px}
.price-values .min{color:#2e8fbf}
.filter-row{height:21px;border-bottom:1px solid var(--line);display:flex;align-items:center;justify-content:space-between;padding:0 11px;font-size:6.8px;color:#555}
.save-btn{position:absolute;left:61px;top:245px;width:65px;height:26px;background:var(--blue);color:var(--white);font-size:6.8px;font-weight:500;display:flex;align-items:center;justify-content:center;gap:4px}

/* projects table */
.projects{left:256px;top:486px;width:361px;height:281px;border:1px solid #d6d6d6}
.projects-head{height:30px;background:var(--blue);color:var(--white);font-size:9.5px;font-weight:500;display:flex;align-items:center;padding:0 10px;gap:0}
.project-row{display:grid;grid-template-columns:120px 92px 74px 73px;height:49.4px;border-bottom:1px solid var(--line)}
.project-row:last-child{border-bottom:none}
.project-row div{display:flex;align-items:center;font-size:6.8px;color:#444;border-right:1px solid var(--line)}
.project-row div:last-child{border-right:none}
.project-row .name{padding:0 11px;line-height:10px;color:#555}
.project-row .num{justify-content:center;font-weight:500;color:#333}

/* testimonials */
.t-title{left:0;top:797px;width:673px;text-align:center;font-size:14px;font-weight:500;color:#333;letter-spacing:.5px}
.t-box{left:94px;top:842px;width:484px;height:124px;background:var(--pale);border:1px solid #cfdde4;border-radius:3px;text-align:center;padding:20px 22px;font-size:7.3px;line-height:14px;color:#555}
.t-tail{left:248px;top:965px}
.t-arrow{top:893px;width:27px;height:27px}
.avatar{left:313px;top:984px;width:46px;height:52px;border:2px solid #e2e2e2;background:linear-gradient(180deg,#7a6a5c,#3b3b40)}
.t-name{left:0;top:1047px;width:673px;text-align:center;font-size:10.5px;color:#444;letter-spacing:.5px}
.t-role{left:0;top:1064px;width:673px;text-align:center;font-size:6.8px;color:#888}

/* footer */
.footer{left:0;top:1101px;width:673px;height:99px;background:var(--footer)}
.social{top:1128px;width:18px;height:18px;border:1px solid #ddd}
.copyright{left:0;top:1162px;width:673px;text-align:center;font-size:6.8px;color:#ddd}
</style>
</head>
<body>
<div class="page">

  <header>
    <div class="abs brand"><span class="brand-name">pelmora</span><span class="brand-dot"></span></div>
    <div class="abs notice">[Notification feed-New items in the feeds are highlighted in blue, and they stay highlighted until cleared.&nbsp; You can clear highlights individually or clear them all at once.]</div>
    <svg class="abs notice-tail" width="14" width="14" height="12" viewBox="0 0 14 12"><path d="M0 0H14L4 12Z" fill="#6bb3cf"/></svg>
    <div class="abs home-btn">
      <svg width="9" height="9" viewBox="0 0 10 10"><path d="M5 1L0.5 5H2V9H4V6.5H6V9H8V5H9.5Z" fill="#fff"/></svg>HOME
    </div>
  </header>

  <nav>
    <div class="abs navbar"></div>
    <div class="abs search">Browse...</div>
    <div class="abs search-btn">
      <svg width="10" height="10" viewBox="0 0 10 10"><circle cx="4" cy="4" r="3" stroke="#fff" stroke-width="1.5" fill="none"/><path d="M6.2 6.2L9 9" stroke="#fff" stroke-width="1.6"/></svg>
    </div>
    <svg class="abs nav-chat" width="16" height="14" viewBox="0 0 16 14"><path d="M0 0H16V10H7L4 14V10H0Z" fill="#6bb3cf"/></svg>
    <span class="abs nav-link" style="left:408px">PROJECTS</span>
    <span class="abs nav-link" style="left:484px">HOW IT WORKS</span>
    <span class="abs nav-link" style="left:571px">MY ACCOUNT</span>
  </nav>

  <section>
    <div class="abs hero" role="img" aria-label="Photo of a smiling young man in glasses and a white shirt outdoors against a blurred green park"></div>
    <h1 class="abs hero-title">CONVERT MORE CUSTOMERS</h1>
    <p class="abs hero-sub">Experience the power of experts<br>collaborating on your project</p>
    <div class="abs hero-btn">GET STARTED</div>
    <div class="abs hero-card">
      <h2>TRUE COLLABORATION AND TEAMWORK</h2>
      <div class="roles">Copywriter Graphic designer Content marketer Creative writer</div>
      <p>There are many variations of passages of Lorem Ipsum available, but the majority have suffered alteration in some form, by injected humour, or randomised words which don't look eve</p>
    </div>
    <svg class="abs hero-tail" width="40" height="28" viewBox="0 0 40 28"><path d="M0 0H40L22 28Z" fill="rgba(40,40,40,.88)"/></svg>
    <span class="abs dot" style="left:310px"></span>
    <span class="abs dot" style="left:332px;background:#222"></span>
    <span class="abs dot" style="left:354px"></span>
  </section>

  <section>
    <div class="abs filters">
      <div class="filters-head">FILTERS
        <svg width="10" height="10" viewBox="0 0 10 10"><path d="M0 0H10L6 5V10L4 9V5Z" fill="#fff"/></svg>
      </div>
      <div class="price">
        <div class="price-label">PRICE</div>
        <div class="slider"><span class="track"></span><span class="fill"></span><span class="knob" style="left:0"></span><span class="knob" style="left:101px"></span></div>
        <div class="price-values"><span class="min">$1,000+ $20</span><span>$1,000+</span></div>
      </div>
      <div class="filter-row">Country<svg width="6" height="4" viewBox="0 0 6 4"><path d="M0 0H6L3 4Z" fill="#eb9b12"/></svg></div>
      <div class="filter-row">Categories<svg width="6" height="4" viewBox="0 0 6 4"><path d="M0 0H6L3 4Z" fill="#eb9b12"/></svg></div>
      <div class="filter-row">Time Left<svg width="6" height="4" viewBox="0 0 6 4"><path d="M0 0H6L3 4Z" fill="#eb9b12"/></svg></div>
      <div class="filter-row">Active | Expired<svg width="6" height="4" viewBox="0 0 6 4"><path d="M0 0H6L3 4Z" fill="#eb9b12"/></svg></div>
      <div class="filter-row">Contains adult content<svg width="6" height="4" viewBox="0 0 6 4"><path d="M0 0H6L3 4Z" fill="#eb9b12"/></svg></div>
      <div class="filter-row">keywords<svg width="6" height="4" viewBox="0 0 6 4"><path d="M0 0H6L3 4Z" fill="#eb9b12"/></svg></div>
      <div class="filter-row">followers<svg width="6" height="4" viewBox="0 0 6 4"><path d="M0 0H6L3 4Z" fill="#eb9b12"/></svg></div>
      <div class="save-btn"><svg width="7" height="7" viewBox="0 0 10 10"><path d="M0 0H10L6 5V10L4 9V5Z" fill="#fff"/></svg>SAVE FILTER</div>
    </div>

    <div class="abs projects">
      <div class="projects-head">
        <span style="width:128px">CROWD PROJECTS:</span>
        <span style="width:81px">SORT: PRICE</span>
        <span style="width:15px">|</span>
        <span style="width:63px">COUNTRY</span>
        <span style="width:15px">|</span>
        <span>TIME LEFT</span>
      </div>
      <div class="project-row"><div class="name">Morbi in ante arcu.<br>Maecenas sit amet sem vel</div><div class="num">$80,</div><div class="num">U.K.</div><div class="num">6 days</div></div>
      <div class="project-row"><div class="name">Lorem ipsum dolor sit amet,<br>consectetur adipiscing</div><div class="num">$90</div><div class="num">C.A.</div><div class="num">6 days</div></div>
      <div class="project-row"><div class="name">Neque porro quisquam est<br>qui dolorem ipsum</div><div class="num">$250,</div><div class="num">U.S.</div><div class="num">6 days</div></div>
      <div class="project-row"><div class="name">Duis ligula sapien, sodales id<br>tortor vitae, ornare</div><div class="num">$62,</div><div class="num">U.K.</div><div class="num">6 days</div></div>
      <div class="project-row"><div class="name">Morbi in ante arcu.<br>Maecenas sit amet sem vel</div><div class="num">$250,</div><div class="num">U.S.</div><div class="num">6 days</div></div>
    </div>
  </section>

  <section>
    <h2 class="abs t-title">TESTIMONIALS</h2>
    <svg class="abs t-arrow" style="left:55px" viewBox="0 0 27 27"><circle cx="13.5" cy="13.5" r="12" fill="#fff" stroke="#ccc" stroke-width="2"/><path d="M18 13.5H10M13 9.5L9 13.5L13 17.5" stroke="#777" stroke-width="2.2" fill="none"/></svg>
    <div class="abs t-box">“With Pelmora I have multiple experts perfecting my content and I only pay for the feedback I find valuable. It's perfect” There are many variations of passages of Lorem Ipsum available, but the majority have suffered alteration in some form, by injected humour, or randomised words which don't look even slightly believable. If you are going to use a passage of Lorem Ipsum, you need to be sure there isn't anything embarrassing hidden in the middle of text. All the Lorem Ipsum generators on the Internet tend to repeat predefined chunks as necessary, making this the first true generator on the Internet.<br>It uses a dictionary of over 200 Latin words, combined with</div>
    <svg class="abs t-tail" width="38" height="30" viewBox="0 0 38 30"><path d="M0 0L36 30V0" fill="#f2f8fb" stroke="#cfdde4"/><path d="M1 0H37" stroke="#f2f8fb" stroke-width="2"/></svg>
    <svg class="abs t-arrow" style="left:591px" viewBox="0 0 27 27"><circle cx="13.5" cy="13.5" r="12" fill="#fff" stroke="#ccc" stroke-width="2"/><path d="M9 13.5H17M14 9.5L18 13.5L14 17.5" stroke="#777" stroke-width="2.2" fill="none"/></svg>
    <div class="abs avatar" role="img" aria-label="Portrait photo of the reviewer in a dark suit"></div>
    <div class="abs t-name">DEAN HARLOW</div>
    <div class="abs t-role">CEO, Ledger Nine</div>
  </section>

  <footer>
    <div class="abs footer"></div>
    <span class="abs social" style="left:290px" aria-label="Social link"></span>
    <span class="abs social" style="left:315px" aria-label="Social link"></span>
    <span class="abs social" style="left:340px" aria-label="Social link"></span>
    <span class="abs social" style="left:365px" aria-label="Social link"></span>
    <p class="abs copyright">Copyright © 2015.pelmora.com - All Rights Reserved&nbsp; - &nbsp;User Agreement, Privacy and Cookies.</p>
  </footer>

</div>
</body>
</html>
```